Tolvane Inc., a third party debt collection agency needs a Website

Tolvane needs a very basic website (3 basic pages) so that consumers can download forms, potential employees can get required EEO language and see potential jobs, and to show that they are a consumer friendly organization.

I've attached a list of requirements and wishes titled "Tolvane Website Specifications"

Target Market(s)

Consumers that need to repay their government loans; Tolvane will walk through the process to assist them.

Industry/Entity Type

Financial Service

Coding

Coded - Design and coding required

Number of Pages Required

1 page

Font styles to use
Sans Serif

Colors
0355a3

Requirements
Must have
• Tolvane Logo
• See document "Tolvane Website Specifications" for all requirements

```html
<!DOCTYPE html>
<html lang="en">
<head>
<meta charset="utf-8">
<title>Tolvane Inc.</title>
<link rel="stylesheet" href="https://fonts.googleapis.com/css2?family=Roboto+Condensed:wght@400;700&family=Open+Sans:wght@400;700&display=swap">
<style>
:root{
  --navy:#26287a;
  --red:#8a1a1c;
  --text:#5a5a5a;
  --line:#d9d9d9;
  --band:#f2f2f2;
  --white:#ffffff;
}
*{margin:0;padding:0;box-sizing:border-box}
html,body{width:763px;height:1200px;overflow:hidden;background:var(--white)}
body{position:relative;font-family:"Open Sans",Arial,sans-serif;color:var(--text)}
.abs{position:absolute}
.cond{font-family:"Roboto Condensed","Arial Narrow",sans-serif}

/* hero */
.hero{left:0;top:0;width:763px;height:480px}
.hero-photo{position:absolute;inset:0;background:linear-gradient(100deg,#f7f8fa 0%,#eef1f5 38%,#c9ccd2 55%,#a8907c 70%,#3d4456 82%,#d8b9a4 100%)}
.brand{left:48px;top:30px;font-size:24px;font-weight:700;color:var(--red)}
.brand-dot{display:inline-block;width:14px;height:14px;border-radius:50%;background:var(--navy);margin-right:8px;vertical-align:middle}
.nav{left:346px;top:36px;display:flex;align-items:center;font-family:"Roboto Condensed",sans-serif;font-size:13px;color:#333}
.nav a{color:inherit;text-decoration:none;display:block;height:33px;line-height:33px}
.nav .active{background:var(--navy);color:var(--white);padding:0 14px;border-radius:2px;margin-right:11px}
.nav .item{margin-right:21px}
.nav .item:last-child{margin-right:0}
.hero-rule{left:48px;top:88px;width:667px;height:1px;background:var(--line)}
.headline{left:50px;top:160px;font-size:30px;line-height:40px;color:var(--navy)}
.advice{left:51px;top:248px;display:flex;align-items:center;color:var(--red)}
.advice .label{font-size:17px;margin-right:8px}
.phone-ring{width:40px;height:40px;border:1.5px solid var(--red);border-radius:50%;display:flex;align-items:center;justify-content:center;margin-right:10px}
.advice .num{font-size:21px;font-weight:700}
.cta{left:49px;top:312px;width:252px;height:40px;background:var(--red);color:var(--white);font-size:16px;line-height:40px;text-align:center;border-radius:2px}

/* welcome */
.welcome-title{left:0;top:510px;width:763px;text-align:center;font-size:30px;color:var(--navy)}
.welcome-title span{color:var(--red)}
.welcome-text{left:95px;top:556px;width:573px;text-align:center;font-size:10.4px;line-height:16px}

.section-title{left:50px;top:650px;font-size:20px;color:var(--navy)}
.section-title span{color:var(--red)}
.quote{left:50px;width:312px}
.avatar{position:absolute;left:0;top:0;width:79px;height:79px;border-radius:50%;border:1.5px solid var(--navy);background:linear-gradient(160deg,#d9d3cc,#8a8684)}
.quote p{position:absolute;left:91px;top:4px;width:222px;font-size:10.4px;line-height:16px}
.quote .who{position:absolute;left:91px;top:86px;font-size:10.4px;font-weight:700;color:var(--red)}
.divider{left:384px;top:642px;width:1px;height:278px;background:var(--line)}
.badge{left:402px;width:96px;background:#dfe7f1;border-radius:4px}
.cred h3{font-weight:400;font-size:15px;line-height:20px;color:var(--navy);font-family:"Open Sans",sans-serif}
.cred p{font-size:10.4px;line-height:16px;margin-top:4px}

/* news */
.news{left:0;top:955px;width:763px;height:166px;background:var(--band)}
.news-title{left:0;top:986px;width:763px;text-align:center;font-size:27px;color:var(--navy)}
.news-title span{color:var(--red)}
.post{top:1032px;width:220px;display:flex}
.date{width:46px;height:54px;background:var(--white);text-align:center;flex:none}
.date b{display:block;font-family:"Roboto Condensed",sans-serif;font-size:21px;color:var(--navy);line-height:22px;padding-top:7px}
.date small{font-size:10px;color:#777}
.post-body{margin-left:7px;font-size:9.6px;line-height:16px}
.post-body a{display:block;color:var(--navy);font-weight:700;text-decoration:none}

/* footer */
.footer{left:0;top:1121px;width:763px;height:79px;background:var(--navy);color:var(--white)}
.foot-links{left:50px;top:1136px;display:flex;gap:26px;font-size:11px;color:var(--white)}
.copy{left:50px;top:1167px;font-size:10px;color:var(--white)}
.social{top:1139px;width:40px;height:40px;border-radius:50%;border:1px solid var(--white)}
.social.filled{background:var(--white)}
</style>
</head>
<body>

<section class="abs hero">
  <div class="hero-photo" role="img" aria-label="Photo of a smiling advisor in a suit helping a client at a desk with a laptop and tablet"></div>
  <div class="abs brand cond"><span class="brand-dot"></span>Tolvane Inc.</div>
  <nav class="abs nav">
    <a class="active" href="#">HOME</a>
    <a class="item" href="#">CONSUMER INFORMATION</a>
    <a class="item" href="#">CAREER</a>
    <a class="item" href="#">CONTACT</a>
  </nav>
  <div class="abs hero-rule"></div>
  <h1 class="abs headline cond" style="font-weight:400">ASSIST CONSUMERS IN<br>RESOLVING THEIR OBLIGATIONS</h1>
  <div class="abs advice cond">
    <span class="label">FREE ADVICE</span>
    <span class="phone-ring">
      <svg width="16" height="16" viewBox="0 0 24 24"><path fill="#8a1a1c" d="M6.6 10.8a15.1 15.1 0 0 0 6.6 6.6l2.2-2.2c.3-.3.7-.4 1-.2 1.1.4 2.3.6 3.6.6.6 0 1 .4 1 1V20c0 .6-.4 1-1 1C10.6 21 3 13.4 3 4c0-.6.4-1 1-1h3.5c.6 0 1 .4 1 1 0 1.3.2 2.5.6 3.6.1.3 0 .7-.2 1z"/></svg>
    </span>
    <span class="num">555 014 2290</span>
  </div>
  <a class="abs cta cond" href="#" style="text-decoration:none">EMPLOYMENT APPLICATION FORM</a>
</section>

<h2 class="abs welcome-title cond" style="font-weight:400">WELCOME TO <span>TOLVANE INC.</span></h2>
<p class="abs welcome-text">Tolvane is a third party debt collection agency that is focused on the collection of higher education loans. Tolvane is compliant with all federal, state, and local laws and is committed to the professional and fair treatment of consumers. Our goal is to assist consumers in resolving their obligations in the manner that best meets their needs and to provide information necessary in order for consumers to make an informed decision.</p>

<h2 class="abs section-title cond" style="font-weight:400">WHAT OUR <span>CLIENT SAY</span></h2>
<div class="abs quote" style="top:692px">
  <div class="avatar" role="img" aria-label="Client portrait"></div>
  <p>Lorem Ipsum is simply dummy text of the printing and typesetting industry. Lorem Ipsum has been the industry's standard dummy text ever since the 1500.</p>
  <span class="who">- CLIENT NAME</span>
</div>
<div class="abs quote" style="top:813px">
  <div class="avatar" role="img" aria-label="Client portrait"></div>
  <p>Lorem Ipsum is simply dummy text of the printing and typesetting industry. Lorem Ipsum has been the industry's standard dummy text ever since the 1500.</p>
  <span class="who">- CLIENT NAME</span>
</div>

<div class="abs divider"></div>

<div class="abs badge" style="top:650px;height:120px" role="img" aria-label="Collectors Guild Alliance member badge"></div>
<div class="abs cred" style="left:522px;top:647px;width:200px">
  <h3>Member of Collectors Guild Alliance</h3>
  <p>Lorem Ipsum is simply dummy text of the printing and typesetting industry. Lorem Ipsum has the industry's standard dummy text ever since the 1500.</p>
</div>
<div class="abs badge" style="top:796px;height:122px" role="img" aria-label="Fair Trade Council accreditation badge"></div>
<div class="abs cred" style="left:509px;top:795px;width:210px">
  <h3>Accredited by the Fair<br>Trade Council</h3>
  <p>Lorem Ipsum is simply dummy text of the printing and typesetting industry. Lorem Ipsum has been the industry's standard dummy text ever since the 1500.</p>
</div>

<div class="abs news"></div>
<h2 class="abs news-title cond" style="font-weight:400">LATEST <span>NEWS</span></h2>
<article class="abs post" style="left:50px">
  <div class="date"><b>21</b><small>Apr</small></div>
  <div class="post-body">Lorem Ipsum is simply dummy text of the print &amp; typesetting industry.<a href="#">READ MORE</a></div>
</article>
<article class="abs post" style="left:277px">
  <div class="date"><b>20</b><small>Apr</small></div>
  <div class="post-body">Lorem Ipsum is simply dummy text of the print &amp; typesetting industry.<a href="#">READ MORE</a></div>
</article>
<article class="abs post" style="left:509px">
  <div class="date"><b>19</b><small>Apr</small></div>
  <div class="post-body">Lorem Ipsum is simply dummy text of the print &amp; typesetting industry.<a href="#">READ MORE</a></div>
</article>

<footer class="abs footer"></footer>
<div class="abs foot-links"><span>Home</span><span>Consumer</span><span>Career</span><span>Discloser</span></div>
<div class="abs copy">© Tolvane Inc. - 2016. All Rights Reserved.</div>
<a class="abs social filled" style="left:561px" href="#" aria-label="Social profile"></a>
<a class="abs social" style="left:614px" href="#" aria-label="Social profile"></a>
<a class="abs social" style="left:674px" href="#" aria-label="Social profile"></a>

</body>
</html>
```